Business Card for brovaLINK

Create a Business Card with an existing logo for brovaLINK AG. We are a Information Technology company that does consulting and developing SW to automate business processes. The main colors are given from the logo.

Industry/Entity Type

Business

Requirements
Nice to have
• we use a a font style Century Gothic in our documents

```html
<!DOCTYPE html>
<html lang="en">
<head>
<meta charset="utf-8">
<title>brovaLINK business card</title>
<link href="https://fonts.googleapis.com/css2?family=Questrial&family=Montserrat:wght@700&display=swap" rel="stylesheet">
<style>
  :root {
    --bg: #e9e6e1;
    --white: #ffffff;
    --blue-deep: #1f3f9e;
    --blue-mid: #1f6fcf;
    --blue-bright: #29a3e6;
    --green: #3cb54a;
    --green-light: #8fd14f;
    --ink: #3c3c3c;
    --name-blue: #2857b8;
  }
  html, body {
    margin: 0;
    padding: 0;
    width: 1200px;
    height: 1024px;
    overflow: hidden;
    background: var(--bg);
    font-family: "Questrial", sans-serif;
  }
  .canvas {
    position: relative;
    width: 1200px;
    height: 1024px;
  }
  .card {
    position: absolute;
    left: 200px;
    width: 800px;
    height: 457px;
    border-radius: 34px;
    overflow: hidden;
    box-shadow: 0 6px 18px rgba(0,0,0,.18);
  }
  .card-front { top: 40px; background: var(--white); }
  .card-back {
    top: 527px;
    background: linear-gradient(135deg, var(--blue-deep) 0%, var(--blue-mid) 45%, var(--blue-bright) 100%);
  }
  .card-front .wave { position: absolute; inset: 0; }
  .holder {
    position: absolute;
    right: 70px;
    top: 28px;
    text-align: right;
  }
  .holder-name {
    font-family: "Montserrat", sans-serif;
    font-weight: 700;
    font-size: 26px;
    line-height: 32px;
    color: var(--name-blue);
    margin: 0;
  }
  .holder-role {
    font-family: "Montserrat", sans-serif;
    font-weight: 700;
    font-size: 17px;
    line-height: 21px;
    color: var(--green);
    margin: 4px 0 0;
  }
  .brand {
    position: absolute;
    display: flex;
    align-items: center;
    gap: 18px;
  }
  .card-front .brand { left: 60px; top: 150px; }
  .brand-dot {
    width: 62px;
    height: 62px;
    border-radius: 50%;
    background: var(--blue-mid);
  }
  .brand-name {
    font-size: 62px;
    color: var(--ink);
    letter-spacing: -1px;
  }
  .contacts {
    position: absolute;
    left: 530px;
    top: 262px;
    list-style: none;
    margin: 0;
    padding: 0;
    color: var(--white);
    font-size: 19px;
    line-height: 30px;
  }
  .contacts li, .address { display: flex; align-items: center; gap: 10px; }
  .contacts svg, .address svg { flex: none; }
  .address {
    position: absolute;
    left: 60px;
    top: 378px;
    color: var(--white);
    font-size: 19px;
    line-height: 27px;
    align-items: flex-start;
  }
  .card-back .brand {
    left: 50%;
    top: 130px;
    transform: translateX(-50%);
    gap: 26px;
  }
  .card-back .brand-dot {
    width: 120px;
    height: 120px;
    background: var(--white);
  }
  .card-back .brand-name {
    font-size: 96px;
    color: var(--white);
  }
  .web {
    position: absolute;
    left: 0;
    right: 0;
    top: 330px;
    text-align: center;
    color: var(--white);
    font-size: 22px;
    letter-spacing: 1px;
  }
</style>
</head>
<body>
<div class="canvas">

  <section class="card card-front">
    <svg class="wave" viewBox="0 0 800 457" width="800" height="457" aria-hidden="true">
      <defs>
        <linearGradient id="blueField" x1="0" y1="1" x2="1" y2="0">
          <stop offset="0" stop-color="var(--blue-deep)"/>
          <stop offset="0.55" stop-color="var(--blue-mid)"/>
          <stop offset="1" stop-color="var(--blue-bright)"/>
        </linearGradient>
        <linearGradient id="greenBand" x1="0" y1="0" x2="1" y2="0">
          <stop offset="0" stop-color="var(--green)"/>
          <stop offset="1" stop-color="var(--green-light)"/>
        </linearGradient>
      </defs>
      <path d="M800,110 C640,110 560,170 470,245 C380,335 220,320 0,318 L0,457 L800,457 Z" fill="url(#greenBand)"/>
      <path d="M800,140 C650,140 580,200 490,270 C400,355 230,350 0,346 L0,457 L800,457 Z" fill="var(--white)"/>
      <path d="M800,146 C655,146 585,206 496,276 C405,362 232,358 0,354 L0,457 L800,457 Z" fill="url(#blueField)"/>
    </svg>

    <div class="holder">
      <p class="holder-name">Jonas Keller</p>
      <p class="holder-role">CEO</p>
    </div>

    <div class="brand">
      <span class="brand-dot"></span>
      <span class="brand-name">brovaLINK</span>
    </div>

    <ul class="contacts">
      <li>
        <svg width="16" height="16" viewBox="0 0 16 16"><path d="M2 5c0-2 2-3 3-3l1 3-1.5 1.2c.8 1.8 2.2 3.2 4 4L10 8.7l3 1c0 1-1 3-3 3C5.6 12.7 2 9.4 2 5z" fill="var(--green-light)"/></svg>
        +41 56 410 20 30
      </li>
      <li>
        <svg width="16" height="16" viewBox="0 0 16 16"><rect x="4" y="1" width="8" height="14" rx="2" fill="var(--green-light)"/><rect x="5.5" y="3" width="5" height="8" fill="var(--blue-mid)"/></svg>
        +41 79 620 45 90
      </li>
      <li>
        <svg width="16" height="16" viewBox="0 0 16 16"><rect x="1" y="3" width="14" height="10" rx="1.5" fill="var(--green-light)"/><path d="M1.5 4 8 9l6.5-5" stroke="var(--blue-mid)" stroke-width="1.4" fill="none"/></svg>
        jonas.keller@brovalink.ch
      </li>
      <li>
        <svg width="16" height="16" viewBox="0 0 16 16"><circle cx="8" cy="8" r="6.5" fill="none" stroke="var(--green-light)" stroke-width="1.6"/><ellipse cx="8" cy="8" rx="2.8" ry="6.5" fill="none" stroke="var(--green-light)" stroke-width="1.3"/><path d="M1.5 8h13" stroke="var(--green-light)" stroke-width="1.3"/></svg>
        www.brovalink.ch
      </li>
    </ul>

    <div class="address">
      <svg width="16" height="20" viewBox="0 0 16 20" style="margin-top:4px"><path d="M8 1a6 6 0 0 0-6 6c0 4.5 6 12 6 12s6-7.5 6-12a6 6 0 0 0-6-6z" fill="var(--green-light)"/><circle cx="8" cy="7" r="2.2" fill="var(--blue-mid)"/></svg>
      <span>Lindenweg 7, 5600 Lenzwil,<br>Switzerland</span>
    </div>
  </section>

  <section class="card card-back">
    <div class="brand">
      <span class="brand-dot"></span>
      <span class="brand-name">brovaLINK</span>
    </div>
    <p class="web">www.brovalink.ch</p>
  </section>

</div>
</body>
</html>
```